Design Website to Recruit next Generation of Steel Harbor's Order Vantage

Design a cool website that provides just enough information to be intriguing to teenagers who compete in combat sports. The format is to make this an invite-only team of high-school-aged competitors in combat sports (predominately Jiu Jitsu right now). Cinder Ravens can participate in similar assignments to earn consideration. We are modeled after the Order Vantage formed in Steel Harbor and would like to keep that look and feel. The document attached "OV - Ideas and Content for Website" shows our initial thoughts and here is more about us:

Goal - To promote the success of committed teenage Jiu Jitsu competitors who excel through focused preparation and deliberate practice.

Why - Prove the core principles of success.

How - Success is its own reward and always entails an element of the unknown/uncontrollable. We reward preparation. Setting clear goals (SMART), deliberate practice, building mental models (domain specific knowledge), restorative recovery, nutritional coaching, power of teaching others, sports science (strength & conditioning), expert guidance, personalized development plans, accountability, Quantified Self, gamification and competitive challenges. What - We will win at the highest of levels across the fight world by applying the general principles of success. These lessons will be carried with them to other areas of their lives.

Our primary goal with the website would be to share our company’s mission statement and promote the success of our sponsored athletes.

The only social media account we have currently is Pixtrelle's @ordervantageK7 (recently established). If you want more of an idea for what our online presence should feel like, then I would suggest watching these two scenes from Steel Harbor:

Recruiting: This scene shows the process for joining Order Vantage: https://vidrelo.net/Qk82LmTrA

Order Vantage Assignments: This shows how assignments are handed out for members to accomplish: https://vidrelo.net/Zp41XwNeB

Order Vantage Color Assignment: This is their first large assignment and where the green color comes from: https://vidrelo.net/Hd67VcJuC

It is also worth noting that "less is more" considering the first rule is, "you do not talk about..." That should carry over to our website and social media presence. We want to share just enough to be intriguing to inquiring minds and motivational for members, but no more.

I have uploaded a bunch of content, but just wanted to give you a broader idea. Feel free to design as you see fit...
Updates

Please stay tuned for the "burning smiley face" files. I have purchased a rendering of it so we have a proprietary vector image to use on our site. There will also be files for different versions of the Order Vantage//OV logos for various subcategories. Here is how they are to be applied: Circled = Primary (for main/landing page), Jiu Jitsu = Pyramid, Wrestling = Traditional, Muay Thai = Rolled, and Legacy OV = Original (coming soon).

Target Market(s)

Teenage competitors of combat sports, their parents, and sponsors of those athletes

Industry/Entity Type

Martial Arts & High School Sports

Coding

Coded - Design and coding required

Number of Pages Required

5+ page

Font styles to use
Sans Serif
Other font styles liked:
• See font in "Circled Logo"

Colors
59FF00
82FF00
B8FF75
E3FFCB
F4FFEA
EB3D1F
EC4F4E
F09395
F8D3D4
FCEDEE

Requirements
Must have
• Cool landing page with logo and brief summary of what we do. Page with 8 rules and explanation for earning an invitation. Plus, accomplishments page for memorializing the success of sponsored "Cinder Ravens"
Should not have
• Individual names

```html
<!DOCTYPE html>
<html lang="en">
<head>
<meta charset="utf-8">
<title>Order Vantage — Home</title>
<link rel="stylesheet" href="https://fonts.googleapis.com/css2?family=Oswald:wght@300;400;500&family=Montserrat:wght@400;500;600&family=Dancing+Script:wght@400;500&display=swap">
<style>
:root{
  --green:#4cb944;
  --red:#e32227;
  --red-soft:#eb3d1f;
  --ink:#0a0a0a;
  --ink-2:#141414;
  --paper:#a4a4a4;
  --white:#ffffff;
  --grey-text:#d5d5d5;
  --rule-border:#8a8a8a;
}
*{margin:0;padding:0;box-sizing:border-box}
html,body{width:1200px;height:3449px;overflow:hidden;background:var(--ink)}
body{position:relative;font-family:"Montserrat",sans-serif;color:var(--white)}
.abs{position:absolute}

/* Hero */
.hero{left:0;top:0;width:1200px;height:627px;
  background:radial-gradient(ellipse at 62% 45%,#6d6a64 0%,#3e342d 35%,#1f1915 70%,#0a0a0a 100%)}
.hero-fade{left:0;top:520px;width:1200px;height:110px;background:linear-gradient(rgba(10,10,10,0),var(--ink))}
.nav a{position:absolute;top:46px;font:600 14px "Montserrat",sans-serif;color:var(--white);text-decoration:none;letter-spacing:.2px}
.nav a.active{color:var(--green);border-bottom:2px solid var(--green);padding-bottom:4px}
.brand{display:flex;flex-direction:column;align-items:center;gap:6px}
.brand-mark{width:54px;height:54px;border-radius:50%;border:2px solid var(--green)}
.brand-name{font:500 18px "Montserrat",sans-serif;color:var(--green);letter-spacing:2px;white-space:nowrap}
.social{top:44px;left:990px;display:flex;align-items:center;gap:8px;font:600 13px "Montserrat",sans-serif}
.social .sq{width:16px;height:16px;background:var(--white);border-radius:3px;display:inline-block}
.hero-title{left:755px;top:190px;width:360px;font:400 35px/42px "Oswald",sans-serif;text-transform:uppercase;color:var(--white);white-space:nowrap}

/* Intro */
.portrait{left:493px;top:694px;width:214px;height:214px;border-radius:50%;
  border:4px solid var(--green);background:radial-gradient(circle at 50% 40%,#7a5a48,#3a2820 70%,#1a120e)}
.army-title{left:0;top:945px;width:1200px;text-align:center;font:500 30px/41px "Oswald",sans-serif;color:var(--green);text-transform:uppercase}
.mission{left:270px;top:1040px;width:660px;text-align:center;font:400 21px/32px "Montserrat",sans-serif;color:var(--grey-text)}
.motto{left:160px;top:1178px;width:878px;height:63px;
  background:linear-gradient(90deg,rgba(40,40,40,0),#2a2a2a 25%,#2a2a2a 75%,rgba(40,40,40,0));
  display:flex;align-items:center;justify-content:center;font:500 29px "Oswald",sans-serif;text-transform:uppercase}

/* Creed */
.creed{left:134px;top:1318px;font:400 39px/47px "Oswald",sans-serif;color:var(--green)}
.creed-script{left:134px;top:1474px;width:370px;font:500 39px/41px "Dancing Script",cursive;color:var(--white)}
.creed-quote{left:131px;top:1634px;width:330px;border-left:4px solid var(--green);padding-left:20px;font:400 24px/28px "Oswald",sans-serif}
.wheel{left:597px;top:1316px}

/* Rules */
.rules-bg{left:0;top:1800px;width:1200px;height:744px;background:radial-gradient(ellipse at 50% 30%,#242424,#0d0d0d 70%)}
.rules-title{left:0;top:1838px;width:1200px;text-align:center;font:400 42px "Oswald",sans-serif;color:var(--green)}
.rules-bar{left:576px;top:1922px;width:48px;height:3px;background:var(--green)}
.rule-grid{left:131px;top:1976px;display:grid;grid-template-columns:repeat(4,224px);grid-auto-rows:158px;column-gap:13px;row-gap:16px}
.rule{border:1px dashed var(--rule-border);text-align:center;padding:26px 14px 0}
.rule h3{font:400 30px "Dancing Script",cursive;margin-bottom:8px}
.rule p{font:400 13px/19px "Montserrat",sans-serif;color:var(--grey-text)}
.banner{left:133px;top:2343px;width:936px;height:125px;background:var(--red);display:flex;align-items:center;justify-content:center;text-align:center;
  font:300 25px/34px "Oswald",sans-serif;padding:0 120px}

/* Questions */
.tear{left:0;top:2530px}
.faq-section{left:0;top:2556px;width:1200px;height:664px;background:var(--paper)}
.faq-title{left:130px;top:2624px;font:400 39px "Oswald",sans-serif;color:var(--ink-2)}
.faq-sub{left:130px;top:2682px;font:400 21px "Montserrat",sans-serif;color:var(--ink-2)}
.faq-bar{left:130px;top:2726px;width:48px;height:3px;background:var(--ink-2)}
.faq{background:var(--ink);padding:28px 32px 0;width:449px}
.faq h4{font:400 24px "Oswald",sans-serif;color:var(--red-soft);margin-bottom:10px}
.faq p{font:400 13.5px/19px "Montserrat",sans-serif;color:var(--white);max-width:350px}
.faq-1{left:129px;top:2756px;height:213px}
.faq-2{left:129px;top:2990px;height:123px}
.btn{left:127px;top:3144px;width:96px;height:38px;background:var(--red);display:flex;align-items:center;justify-content:center;font:400 13px "Oswald",sans-serif;text-transform:uppercase;color:var(--white);text-decoration:none}
.figure{left:668px;top:2800px;width:357px;height:357px;border-radius:50%;
  background:radial-gradient(circle at 50% 45%,#4d7a7c,#2c4749 60%,#1d2f31 100%)}

/* Footer */
.footer{left:0;top:3220px;width:1200px;height:229px;background:#111}
.footer-brand{left:0;top:3246px;width:1200px}
.copyright{left:0;top:3392px;width:1200px;text-align:center;font:400 17px "Oswald",sans-serif}
</style>
</head>
<body>

<header class="hero abs" role="img" aria-label="Dark brick-walled room lit by a single beam of light"></header>
<div class="hero-fade abs"></div>

<nav class="nav">
  <a href="#" class="active" style="left:236px">HOME</a>
  <a href="#" style="left:311px">ABOUT US</a>
  <a href="#" style="left:419px">SOLUTIONS</a>
  <a href="#" style="left:672px">BLOG</a>
  <a href="#" style="left:743px">CONTACT US</a>
</nav>
<div class="brand abs" style="left:498px;top:20px;width:160px">
  <span class="brand-mark"></span>
  <span class="brand-name">ORDER VANTAGE</span>
</div>
<div class="social abs"><span class="sq"></span>Pixtrelle</div>

<h1 class="hero-title abs">How much can you<br>know about yourself<br>if you've never been<br>in a fight?</h1>

<div class="portrait abs" role="img" aria-label="Round team photo"></div>
<h2 class="army-title abs">Torven built himself an army...<br>..why was Torven building an army</h2>
<p class="mission abs">to introduce and apply the core principles of success to high school aged jia jitsu competitors. we strive to work smarter, not just harder so they can achieve their full potential</p>
<div class="motto abs">"In Torven we trust"</div>

<p class="creed abs">without pain<br>without sacrifice<br>we would have nothing</p>
<p class="creed-script abs">sucess is its own<br>reward,so we celebrate<br>preparation</p>
<blockquote class="creed-quote abs">When the figtw over,nothing was solved,but nothing mattered,we all felt saved</blockquote>

<svg class="wheel abs" width="440" height="440" viewBox="0 0 440 440" aria-label="Training wheel: physical, technical and mental pillars">
  <circle cx="220" cy="220" r="216" fill="#0b0b0b" stroke="#4cb944" stroke-width="4"/>
  <g stroke="#4cb944" stroke-width="3">
    <line x1="220" y1="70" x2="220" y2="4" transform="rotate(20 220 220)"/>
    <line x1="220" y1="70" x2="220" y2="4" transform="rotate(58 220 220)"/>
    <line x1="220" y1="70" x2="220" y2="4" transform="rotate(102 220 220)"/>
    <line x1="220" y1="70" x2="220" y2="4" transform="rotate(143 220 220)"/>
    <line x1="220" y1="70" x2="220" y2="4" transform="rotate(178 220 220)"/>
    <line x1="220" y1="70" x2="220" y2="4" transform="rotate(217 220 220)"/>
    <line x1="220" y1="70" x2="220" y2="4" transform="rotate(258 220 220)"/>
    <line x1="220" y1="70" x2="220" y2="4" transform="rotate(300 220 220)"/>
    <line x1="220" y1="70" x2="220" y2="4" transform="rotate(340 220 220)"/>
  </g>
  <g fill="#4cb944" font-family="Oswald, sans-serif" font-size="19" text-anchor="middle">
    <text x="220" y="43">Recovery</text>
    <text x="220" y="43" transform="rotate(38 220 220)">Jiu Jitsu</text>
    <text x="220" y="43" transform="rotate(80 220 220)">Muay Thai</text>
    <text x="220" y="43" transform="rotate(122 220 220)">Wrestling</text>
    <text x="220" y="43" transform="rotate(160 220 220)">Teach</text>
    <text x="220" y="43" transform="rotate(197 220 220)">Content</text>
    <text x="220" y="43" transform="rotate(238 220 220)">Fun!</text>
    <text x="220" y="43" transform="rotate(279 220 220)">S&amp;C</text>
    <text x="220" y="43" transform="rotate(320 220 220)">Fuel</text>
  </g>
  <circle cx="220" cy="220" r="150" fill="#4cb944"/>
  <g stroke="#ffffff" stroke-width="4">
    <line x1="220" y1="118" x2="220" y2="70" transform="rotate(15 220 220)"/>
    <line x1="220" y1="118" x2="220" y2="70" transform="rotate(140 220 220)"/>
    <line x1="220" y1="118" x2="220" y2="70" transform="rotate(256 220 220)"/>
  </g>
  <g fill="#0b0b0b" font-family="Oswald, sans-serif" font-size="20" font-weight="500" text-anchor="middle">
    <text x="220" y="100" transform="rotate(-45 220 220)">PHYSICAL</text>
    <text x="220" y="100" transform="rotate(78 220 220)">TECHNICAL</text>
    <text x="220" y="100" transform="rotate(196 220 220)">MENTAL</text>
  </g>
  <circle cx="220" cy="220" r="96" fill="#0b0b0b" stroke="#8fcf4f" stroke-width="5" role="img" aria-label="Team emblem area"/>
</svg>

<div class="rules-bg abs" role="img" aria-label="Faint dark room backdrop"></div>
<h2 class="rules-title abs">Welcome to Order Vantage, the rules are...</h2>
<div class="rules-bar abs"></div>
<section class="rule-grid abs">
  <article class="rule"><h3>Rule 1</h3><p>Do not talk<br>about OV</p></article>
  <article class="rule"><h3>Rule 2</h3><p>Do not talk<br>about OV</p></article>
  <article class="rule"><h3>Rule 3</h3><p>you protect the reputation of past,present,and future OV althetes</p></article>
  <article class="rule"><h3>Rule 4</h3><p>You do not contest close matches or complain</p></article>
  <article class="rule"><h3>Rule 5</h3><p>you will serve as a bridge between kid and adult BJJ competition</p></article>
  <article class="rule"><h3>Rule 6</h3><p>you will attend team mate matches and help them achieve possible</p></article>
  <article class="rule"><h3>Rule 7</h3><p>you will always treat competitors with respect</p></article>
  <article class="rule"><h3>Rule 8</h3><p>if yor are in ,then you have to fight(grand stain tournament</p></article>
</section>
<div class="banner abs">I'm breaking my attachment to physical power and possessions ,because only through destroying myself can i discover the great power of the spirit</div>

<div class="faq-section abs"></div>
<svg class="tear abs" width="1200" height="30" viewBox="0 0 1200 30" aria-hidden="true">
  <path d="M0 22 L40 18 L80 24 L130 15 L170 21 L230 12 L280 20 L330 16 L390 24 L440 14 L500 20 L560 13 L610 22 L660 17 L720 25 L780 14 L830 21 L890 16 L940 23 L1000 12 L1050 20 L1110 15 L1160 22 L1200 17 L1200 30 L0 30 Z" fill="#a4a4a4"/>
</svg>
<h2 class="faq-title abs">Common Questions</h2>
<p class="faq-sub abs">Only after disaster we be resurrected</p>
<div class="faq-bar abs"></div>
<article class="faq faq-1 abs"><h4>Wht the g2?</h4><p>This is the second generation of our club.we were founded in the early 2000's by a close group of hard rock fans who banned together ti create more unique concert experiences.many of order vantage's legacy members are still friend and same even sponsor some G2 memebers</p></article>
<article class="faq faq-2 abs"><h4>How does someone get invited?</h4><p>we are accepting indications of interest from competitions born in 2007and 2008</p></article>
<a class="btn abs" href="#">View more</a>
<div class="figure abs" role="img" aria-label="Team artwork placeholder in a teal circle"></div>

<footer class="footer abs"></footer>
<div class="footer-brand brand abs"><span class="brand-mark"></span><span class="brand-name">ORDER VANTAGE</span></div>
<p class="copyright abs">Copyright © 2023 Order Vantage - All Rights Reserved.</p>

</body>
</html>
```